Business Card & Email Signature Design || Upmarket + Luxury

Rima Vale Honey, a New Zealand Manuka Honey company needs a Business Card & Email Signature design.

Our logo's are attached in Gold & Black versions, feel free to be creative with how you use the logo and it's patterns in your design.

Style:
- Looking for an Elegant, Luxurious, Upmarket feel.
- Black/Matte Black Card, Gold Foil, UV Embossing

Information to Add:

- Logo
- Company Name: Rima Vale Honey
- Name: Martin Holloway
- Title: Creative Director
- Phone: +64 2815 96 417
- Email: martin@rimavalehoney.example.nz
- Website: www.rimavalehoney.example.nz

- Socials: ***For email Signature Only***
- Facebook: https://www.facebook.com/rimavalehoney/
- Instagram: https://www.instagram.com/rimavalehoney/

Target Market(s)

Asia/Europe Luxury, Upmarket

Contact Information for Business Card

- Logo
- Name: Martin Holloway
- Phone: +64 2815 96 417

Font styles to use
Other font styles liked:
• Champagne & Limousines (Attached)

Requirements
Must have
• Business Card & Email Signature Design.

Looking for a Sleek, Luxury, Upmarket Design.

```html
<!DOCTYPE html>
<html lang="en">
<head>
<meta charset="utf-8">
<title>Rima Vale Honey — Business Card</title>
<link href="https://fonts.googleapis.com/css2?family=Poppins:wght@300;400;600&display=swap" rel="stylesheet">
<style>
  :root {
    --stage: #1b1b1b;
    --card-white: #ffffff;
    --card-black: #121212;
    --ink: #2b2b2b;
    --ink-soft: #555555;
    --gold: #d8b458;
    --pattern: #1c1c1c;
  }
  * { margin: 0; padding: 0; box-sizing: border-box; }
  html, body { width: 1200px; height: 909px; overflow: hidden; }
  body {
    background: var(--stage);
    font-family: "Poppins", sans-serif;
    position: relative;
  }
  .card {
    position: absolute;
    left: 290px;
    width: 620px;
    height: 354px;
    overflow: hidden;
    box-shadow: 0 18px 40px rgba(0,0,0,.55);
  }
  .card--front { top: 62px; background: var(--card-white); color: var(--ink); }
  .card--back { top: 484px; background: var(--card-black); }

  .contact { position: absolute; left: 44px; top: 96px; }
  .contact__name { font-weight: 600; font-size: 17px; letter-spacing: .5px; text-transform: uppercase; }
  .contact__title { font-weight: 300; font-size: 13px; color: var(--ink-soft); margin-top: 1px; }
  .contact__list { list-style: none; margin-top: 12px; }
  .contact__item { display: flex; align-items: center; gap: 10px; font-weight: 300; font-size: 12.5px; line-height: 21px; letter-spacing: .3px; }
  .contact__icon { width: 11px; height: 11px; fill: var(--ink); flex: none; }

  .divider { position: absolute; left: 236px; top: 140px; width: 300px; height: 1px; background: var(--ink); transform: rotate(0deg); }

  .wordmark {
    position: absolute;
    display: flex; align-items: center; gap: 12px;
    font-family: "Poppins", sans-serif;
    font-weight: 400;
    text-transform: uppercase;
    letter-spacing: 4px;
    white-space: nowrap;
  }
  .wordmark__dot { width: 14px; height: 14px; border-radius: 50%; flex: none; }
  .card--front .wordmark { right: 44px; top: 96px; font-size: 17px; color: var(--ink); }
  .card--front .wordmark__dot { background: var(--ink); }
  .footer-name { position: absolute; right: 84px; bottom: 40px; font-weight: 300; font-size: 12px; letter-spacing: 1px; text-transform: uppercase; color: var(--ink-soft); }

  .pattern-field {
    position: absolute; inset: 0;
    background: radial-gradient(ellipse at 62% 40%, var(--pattern) 0%, var(--card-black) 70%);
  }
  .card--back .wordmark { left: 50%; top: 50%; transform: translate(-50%, -50%); font-size: 22px; color: var(--gold); }
  .card--back .wordmark__dot { background: var(--gold); }
</style>
</head>
<body>
  <section class="card card--front" aria-label="Business card front">
    <div class="contact">
      <p class="contact__name">Martin Holloway</p>
      <p class="contact__title">Creative Director</p>
      <ul class="contact__list">
        <li class="contact__item">
          <svg class="contact__icon" viewBox="0 0 24 24" aria-hidden="true"><path d="M6.6 10.8a15.1 15.1 0 0 0 6.6 6.6l2.2-2.2a1 1 0 0 1 1-.25 11.4 11.4 0 0 0 3.6.57 1 1 0 0 1 1 1V20a1 1 0 0 1-1 1A17 17 0 0 1 3 4a1 1 0 0 1 1-1h3.5a1 1 0 0 1 1 1c0 1.25.2 2.45.57 3.57a1 1 0 0 1-.25 1z"/></svg>
          +64 2815 96 417
        </li>
        <li class="contact__item">
          <svg class="contact__icon" viewBox="0 0 24 24" aria-hidden="true"><path d="M2 5h20v14H2z M2 5l10 8 10-8" fill="none" stroke="#2b2b2b" stroke-width="2"/></svg>
          martin@rimavalehoney.example.nz
        </li>
        <li class="contact__item">
          <svg class="contact__icon" viewBox="0 0 24 24" aria-hidden="true"><circle cx="12" cy="12" r="10" fill="none" stroke="#2b2b2b" stroke-width="2"/><path d="M2 12h20M12 2c3 3 3 17 0 20M12 2c-3 3-3 17 0 20" fill="none" stroke="#2b2b2b" stroke-width="1.6"/></svg>
          www.rimavalehoney.example.nz
        </li>
      </ul>
    </div>
    <div class="divider" aria-hidden="true"></div>
    <div class="wordmark"><span class="wordmark__dot" aria-hidden="true"></span>Rima Vale Honey</div>
    <p class="footer-name">Rima Vale Honey</p>
  </section>

  <section class="card card--back" aria-label="Business card back">
    <div class="pattern-field" role="img" aria-label="Faint tone-on-tone swirl pattern across the black card"></div>
    <div class="wordmark"><span class="wordmark__dot" aria-hidden="true"></span>Rima Vale Honey</div>
  </section>
</body>
</html>
```